Animal Horse & Bedding Company Needs a Website Coded & Designed

We need a website for a new animal bedding and feed company that is visually grabbing and vibrant. We would like to see a website that displays trust, quality and confidence. Needs to be responsive and mobile friendly for all browsers and coded for both Android & IOS. SEO is also important.

Joomla or Wordpress – must be both desktop and mobile friendly with fast page load speed. Need the ability to edit ourselves in Wordpress or Joomla.

Full details attached below with some layout and content ideas.

Coding

Coded - Design and coding required

Number of Pages Required

5+ page

Font styles to use
Sans Serif

Requirements
Must have
• Needs to be responsive and mobile friendly for all browsers and coded for both Android & IOS. SEO is also important.

Wordpress – must be both desktop and mobile friendly with fast page load speed. Need the ability to edit ourselves in Wordpress.

Logo Colours:
Dark Brown
CMYK: 50 / 70 / 80 / 70
Pantone: 4625C

Orange
CMYK: 0 / 50 / 100 / 0
Pantone: 144C
Nice to have
• Use picture of building attached and super impose logo on building.

```html
<!DOCTYPE html>
<html lang="en">
<head>
<meta charset="UTF-8">
<title>Golden Bale – Bedding &amp; Feed</title>
<link href="https://fonts.googleapis.com/css2?family=Roboto:ital,wght@0,300;0,400;0,500;0,700;1,400&display=swap" rel="stylesheet">
<style>
:root{
  --orange:#f7941d;
  --brown:#4a2e1f;
  --ink:#111;
  --text:#666;
  --white:#fff;
  --line:#e6e6e6;
}
*{margin:0;padding:0;box-sizing:border-box}
html,body{width:1200px;height:3421px;overflow:hidden;background:var(--white);font-family:'Roboto',sans-serif;color:var(--ink)}
.page{position:relative;width:1200px;height:3421px}
.abs{position:absolute}
.btn{position:absolute;display:flex;align-items:center;justify-content:center;background:var(--orange);color:var(--white);border-radius:30px;font-weight:700;font-size:14px;letter-spacing:.3px;text-transform:uppercase}

/* header */
.header{position:absolute;left:0;top:0;width:1200px;height:81px;background:var(--white)}
.logo{position:absolute;left:89px;top:20px;display:flex;align-items:center;gap:12px}
.logo-dot{width:40px;height:40px;border-radius:50%;background:var(--orange)}
.logo-name{font-size:30px;font-weight:500;color:var(--brown);letter-spacing:1px;text-transform:uppercase}
.nav{position:absolute;top:32px;font-size:14px;color:var(--ink);text-transform:uppercase}
.nav.active{color:var(--orange)}

/* hero */
.hero{position:absolute;left:0;top:81px;width:1200px;height:632px;background:linear-gradient(180deg,#c7cfd6 0%,#aab3b6 22%,#5e6a4c 40%,#6a6150 60%,#4b4a42 100%)}
.hero-shade{position:absolute;inset:0;background:rgba(0,0,0,.25)}
.hero-title{position:absolute;left:0;width:1200px;top:210px;text-align:center;color:var(--white);font-size:64px;font-weight:700}
.hero-sub{position:absolute;left:0;width:1200px;top:292px;text-align:center;color:var(--white);font-size:34px;font-weight:400;letter-spacing:20px;text-indent:20px}

/* intro */
.intro-img{position:absolute;left:89px;top:802px;width:484px;height:475px;background:linear-gradient(135deg,#8a6a3c,#c98a3e 45%,#6d5a3e)}
.intro-text{position:absolute;left:597px;top:845px;width:511px;font-size:16px;line-height:26.8px;color:var(--text);font-weight:300;text-align:justify}
.intro-text p{margin-bottom:27px}

/* features */
.feature{position:absolute;top:1367px;width:330px;text-align:center}
.feature svg{display:block;margin:0 auto}
.feature h3{margin-top:26px;font-size:20px;font-weight:500;color:var(--ink)}
.feature p{margin-top:14px;font-size:14px;line-height:23px;color:var(--text);font-weight:300}

/* split band */
.band{position:absolute;top:1639px;height:581px}
.band-bed{left:0;width:595px;background:linear-gradient(135deg,#6f8290,#8a98a2 50%,#b7b2a6)}
.band-feed{left:595px;width:605px;background:linear-gradient(135deg,#5e4a3c,#6b6662 50%,#4a4a4a)}
.band-shade{position:absolute;inset:0;background:rgba(0,0,0,.28)}
.band h2{position:absolute;top:76px;font-size:37px;font-weight:700;color:var(--white)}
.band .tag{position:absolute;top:127px;font-size:16px;font-style:italic;color:var(--white);font-weight:300}
.band ul{position:absolute;top:166px;list-style:none}
.band li{position:relative;padding-left:32px;height:28.7px;font-size:16px;color:var(--white)}
.band li::before{content:"»";position:absolute;left:0;top:-1px;font-size:17px}

/* delivery */
.delivery h2{position:absolute;left:89px;top:2326px;font-size:32px;font-weight:700}
.delivery-text{position:absolute;left:89px;top:2384px;width:509px;font-size:16.5px;line-height:26.8px;color:var(--text);font-weight:300;text-align:justify}
.delivery-text p{margin-bottom:27px}
.delivery-img{position:absolute;left:624px;top:2312px;width:484px;height:475px;background:linear-gradient(135deg,#4c3a2e,#8a5c3a 45%,#b9b4a8)}

/* newsletter */
.newsletter{position:absolute;left:0;top:2877px;width:1200px;height:341px;background:linear-gradient(135deg,#f0921e,#e98a1a 50%,#f39a2a)}
.newsletter h2{position:absolute;left:0;width:1200px;top:84px;text-align:center;font-size:32px;font-weight:700;color:var(--white)}
.newsletter .lead{position:absolute;left:290px;width:620px;top:136px;text-align:center;font-size:16px;line-height:24px;color:var(--white)}
.field{position:absolute;left:240px;top:198px;width:720px;height:53px;background:var(--white);border-radius:30px}
.field span{position:absolute;left:28px;top:17px;font-size:16px;color:#666}
.subscribe{position:absolute;right:0;top:0;width:164px;height:53px;border-radius:30px;background:var(--ink);color:var(--white);display:flex;align-items:center;justify-content:center;font-size:16px;font-weight:500}

/* footer */
.social{position:absolute;top:3311px;width:14px;height:14px;border-radius:50%;background:#555}
.foot-link{position:absolute;top:3346px;font-size:14px;color:#555}
.copy{position:absolute;left:0;width:1200px;top:3384px;text-align:center;font-size:12.5px;color:#555}
</style>
</head>
<body>
<div class="page">

  <header class="header">
    <div class="logo"><div class="logo-dot"></div><div class="logo-name">Golden Bale</div></div>
    <div class="nav active" style="left:475px">Home</div>
    <div class="nav" style="left:551px">About</div>
    <div class="nav" style="left:633px">Feed</div>
    <div class="nav" style="left:702px">Bedding</div>
    <div class="nav" style="left:799px">Contact Us</div>
    <div class="btn" style="left:933px;top:17px;width:175px;height:45px">Request Quote</div>
  </header>

  <section class="hero" role="img" aria-label="Aerial view of red farm barns and paddocks under a cloudy sky">
    <div class="hero-shade"></div>
    <div class="hero-title">GOLDEN BALE</div>
    <div class="hero-sub">BEDDING &amp; FEED</div>
    <div class="btn" style="left:512px;top:360px;width:175px;height:44px">Request Quote</div>
  </section>

  <section class="intro">
    <div class="intro-img" role="img" aria-label="Hens eating grain from open hands"></div>
    <div class="intro-text">
      <p>Looking for the best bedding and feed for your horse, livestock or household pet look no further.&nbsp; We use premium locally sourced straw and hay in all of our products and are committed in providing quality products and service.</p>
      <p>Your animal deserves the very best in health and comfort to keep them healthy, strong and happy.&nbsp; Our products are designed for horses, livestock (goats, cattle and sheep), small caged animals (rabbits, guinea pigs and more).</p>
      <p>Golden Bale offers supply and delivery of fresh bedding as well as removal of waste bedding.&nbsp; Let us deliver you a container of fresh straw and haul your waste bedding away.&nbsp; A full service solution that is sustainable and responsible.</p>
    </div>
  </section>

  <section class="features">
    <div class="feature" style="left:63px">
      <svg width="70" height="76" viewBox="0 0 70 76" fill="none" stroke="#f7941d" stroke-width="2.5"><circle cx="32" cy="32" r="24"/><circle cx="32" cy="32" r="16"/><path d="M24 32l6 6 20-22"/><path d="M18 52l-8 18 10-4 5 8 7-18M46 52l8 18-10-4-5 8-7-18"/></svg>
      <h3>Quality Guaranteed</h3>
      <p>Grown for quality - 100% natural with no<br>chemicals or additives</p>
    </div>
    <div class="feature" style="left:431px">
      <svg width="78" height="76" viewBox="0 0 78 76" fill="none" stroke="#f7941d" stroke-width="2.5"><rect x="4" y="4" width="24" height="18"/><path d="M4 4l12 10 12-10"/><rect x="12" y="26" width="54" height="34"/><circle cx="39" cy="40" r="10"/><path d="M29 40h20M39 30v20"/><circle cx="64" cy="12" r="8"/><path d="M28 72h24M39 60v12"/></svg>
      <h3>Full Service Solution</h3>
      <p>Dedicated in providing a full service solution of<br>bedding supply &amp; waste removal</p>
    </div>
    <div class="feature" style="left:800px">
      <svg width="78" height="76" viewBox="0 0 78 76" fill="none" stroke="#f7941d" stroke-width="2.5"><circle cx="44" cy="30" r="14"/><path d="M40 8h8l-4 8zM44 22v16"/><circle cx="62" cy="52" r="8"/><path d="M4 50h12v22H4zM16 54h14c6 0 8 6 2 6H24M16 70h24l26-16"/></svg>
      <h3>Convenient &amp; Cost Effective</h3>
      <p>Compressed bags , pellets or bulk products<br>saving in shipping costs</p>
    </div>
  </section>

  <section class="band band-bed" role="img" aria-label="Kitten resting on a knitted blanket">
    <div class="band-shade"></div>
    <h2 style="left:88px">Bedding</h2>
    <div class="tag" style="left:90px">Benefits</div>
    <ul style="left:90px">
      <li>100% Natural Chopped Straw</li>
      <li>Low Dust</li>
      <li>Chemical &amp; Additive Free</li>
      <li>Clean &amp; Highly Absorbent</li>
      <li>Cheaper than Wood Shavings</li>
      <li>Economic – less used and less wasted</li>
      <li>Environmentally Friendly – Recyclable &amp; Compostable</li>
    </ul>
    <div class="btn" style="left:90px;top:393px;width:175px;height:45px">Read More</div>
  </section>

  <section class="band band-feed" role="img" aria-label="Cat eating from a bowl on a wooden floor">
    <div class="band-shade"></div>
    <h2 style="left:103px">Feed</h2>
    <div class="tag" style="left:104px">Benefits</div>
    <ul style="left:104px">
      <li>100% Natural</li>
      <li>Chemical &amp; Additive Free</li>
      <li>Available in Pellets or Cubes</li>
      <li>High Protein Content</li>
      <li>Eliminate Waste In Feeding</li>
      <li>Clean - Eliminates Dust From Feeding Baled Hay</li>
      <li>Cost Effective</li>
      <li>Convenient</li>
      <li>Less wasted feed</li>
    </ul>
    <div class="btn" style="left:104px;top:446px;width:175px;height:45px">Read More</div>
  </section>

  <section class="delivery">
    <h2>Delivery in Canada &amp; USA</h2>
    <div class="delivery-text">
      <p>Lorem ipsum dolor sit amet, consectetur adipiscing elit, sed do eiusmod tempor incididunt ut labore et dolore magna aliqua. Ut enim ad minim veniam, quis nostrud exercitation ullamco laboris nisi ut aliquip ex ea commodo consequat. Duis aute irure dolor in reprehenderit in voluptate velit esse cillum dolore eu fugiat nulla pariatur. Excepteur sint occæcat cupidatat non proident, sunt in culpa qui officia deserunt mollit anim id est laborum.</p>
      <p>Lorem ipsum dolor sit amet, consectetur adipiscing elit, sed do eiusmod tempor incididunt ut labore et dolore magna aliqua. Ut enim ad minim veniam, quis nostrud exercitation ullamco laboris nisi ut aliquip ex ea commodo consequat. Duis aute irure dolor in reprehenderit in voluptate velit esse cillum dolore eu fugiat nulla pariatur.</p>
    </div>
    <div class="delivery-img" role="img" aria-label="Horse drinking from a metal bucket at a fence"></div>
  </section>

  <section class="newsletter" role="img" aria-label="Orange-toned photo of a resting puppy">
    <h2>Newsletter Sign Up</h2>
    <div class="lead">Lorem ipsum dolor sit amet, consectetur adipiscing elit, sed do eiusmod tempor incididunt ut labore et dolore magna aliqua</div>
    <div class="field"><span>Enter Your Email Address</span><div class="subscribe">SUBSCRIBE</div></div>
  </section>

  <footer>
    <div class="social" style="left:553px"></div>
    <div class="social" style="left:590px"></div>
    <div class="social" style="left:630px"></div>
    <div class="foot-link" style="left:388px">Home</div>
    <div class="foot-link" style="left:474px">About</div>
    <div class="foot-link" style="left:560px">Feed</div>
    <div class="foot-link" style="left:637px">Bedding</div>
    <div class="foot-link" style="left:738px">Contact Us</div>
    <div class="copy">© Copyrights.2021.The Company Name.All Rights Reserved</div>
  </footer>

</div>
</body>
</html>
```